Kestrel Facilities Business Card Design

We would now like to design business cards with the new Kestrel Facilities logo

Target Market(s)

Professional

Industry/Entity Type

Professional services

Contact Information for Business Card

Employee name, title, phone number, email address, corporate office address and logo.

Font styles to use
Sans Serif

Colors
0054AA
0677BA
7BADD7
CADEEF
E8F1F8

Requirements
Must have
• My logo
Should not have
• any other pictures or images besides my logo

```html
<!DOCTYPE html>
<html lang="en">
<head>
<meta charset="utf-8">
<title>Kestrel Facilities – Business Card</title>
<link href="https://fonts.googleapis.com/css2?family=Montserrat:wght@400;500;700&display=swap" rel="stylesheet">
<style>
  :root {
    --brand-blue: #3475ba;
    --wave-grey: #a3a1a2;
    --card-white: #ffffff;
    --ink: #1a1a1a;
    --backdrop: #e9e9e9;
  }
  html, body {
    margin: 0;
    padding: 0;
    width: 1160px;
    height: 1200px;
    overflow: hidden;
    background: var(--backdrop);
  }
  .canvas {
    position: relative;
    width: 1160px;
    height: 1200px;
  }
  .card {
    position: absolute;
    left: 199px;
    width: 778px;
    height: 442px;
    background: var(--card-white);
  }
  .card--front { top: 105px; }
  .card--back  { top: 634px; }
  .card svg { display: block; width: 100%; height: 100%; }
  .name   { font: 700 54px "Montserrat", sans-serif; fill: var(--card-white); letter-spacing: -0.5px; }
  .title  { font: 400 34px "Montserrat", sans-serif; fill: var(--card-white); }
  .detail { font: 400 34px "Montserrat", sans-serif; fill: var(--ink); }
  .brand-name { font: 500 64px "Montserrat", sans-serif; fill: var(--brand-blue); }
  .wave-blue { fill: var(--brand-blue); }
  .wave-grey { fill: var(--wave-grey); }
  .icon { fill: var(--brand-blue); }
</style>
</head>
<body>
<main class="canvas">

  <section class="card card--front" aria-label="Business card front">
    <svg viewBox="0 0 1271 722" xmlns="http://www.w3.org/2000/svg">
      <path class="wave-grey" d="M0,158 C300,268 600,205 900,92 C1000,55 1060,44 1110,42 C1000,52 860,112 715,190 C565,270 400,330 0,266 Z"/>
      <path class="wave-blue" d="M0,0 H1271 V80 C1150,22 1000,25 800,92 C550,172 340,250 0,138 Z"/>
      <path class="wave-blue" d="M543,262 C750,145 950,62 1110,58 C1180,56 1220,70 1248,88 C1150,62 1000,72 860,152 C760,212 650,282 548,325 Z"/>

      <text class="name" x="55" y="94">DANA WHITLOCK</text>
      <text class="title" x="55" y="138">Co-Founder</text>

      <text class="detail" x="52" y="400">4180 N. Harbor Avenue</text>
      <text class="detail" x="52" y="447">Suite 620 Lakeview.14</text>

      <g class="icon" transform="translate(53,508)">
        <path d="M2,10 C2,3 30,3 30,10 L30,14 L24,14 L24,10 L8,10 L8,14 L2,14 Z"/>
        <rect x="7" y="14" width="18" height="14" rx="2"/>
      </g>
      <text class="detail" x="95" y="534">+254-203-47150</text>

      <g class="icon" transform="translate(53,562)">
        <rect x="0" y="0" width="32" height="22" rx="2"/>
        <path d="M2,2 L16,13 L30,2" fill="none" stroke="#fff" stroke-width="2.5"/>
      </g>
      <text class="detail" x="95" y="582">info@kestrelfac.com</text>

      <g transform="translate(69,620)">
        <circle class="icon" r="15"/>
        <path d="M-8,-8 C-2,-6 -2,0 -8,2 M4,-12 C0,-6 8,-2 10,2 M-2,6 C2,4 6,8 2,13" fill="none" stroke="#fff" stroke-width="2.5"/>
      </g>
      <text class="detail" x="95" y="630">www.kestrelfac.com</text>

      <rect class="icon" x="745" y="424" width="40" height="40"/>
      <text class="brand-name" x="805" y="440">Kestrel</text>
      <text class="brand-name" x="805" y="512">Facilities</text>
    </svg>
  </section>

  <section class="card card--back" aria-label="Business card back">
    <svg viewBox="0 0 1271 722" xmlns="http://www.w3.org/2000/svg">
      <rect class="icon" x="380" y="320" width="56" height="56"/>
      <text class="brand-name" x="462" y="340" style="font-size:84px">Kestrel</text>
      <text class="brand-name" x="462" y="432" style="font-size:84px">Facilities</text>
    </svg>
  </section>

</main>
</body>
</html>
```